Corporate Design für eine Veranstaltungsagentur
Vielen Dank an Bartholomä, der trotz vieler unserer Revisionswünsche stets freundlich war, professionell und schnell gearbeitet hat und uns am Ende ein wirklich wunderbares Ergebnis geliefert hat! :-) Wir können ihn uneingeschränkt weiterempfehlen!
Zielgruppe
Agentur zur Planung, Organisation und Durchführung von Veranstaltungen aller Art
Ingenieurbetrieb für Veranstaltungstechnik und - produktion
Organisation und Durchführung der 'Wellenklang'-Veranstaltungsreihe: www.wellenklang-turnier.de
Zielgruppe:
Personen jeder Altersgruppe, Privatpersonen, Geschäftskunden
Aufgabenstellung
Die Farbe Grün sollte beibehalten werden.
Logo soll Professionalität und Innovation ausstrahlen, gleichzeitig modern und zeitlos wirken.

```html
<!DOCTYPE html>
<html lang="de">
<head>
<meta charset="utf-8">
<title>Veranto Events – Geschäftsausstattung</title>
<link href="https://fonts.googleapis.com/css2?family=Mada:wght@400;500;600&family=Open+Sans:wght@400;600;700&display=swap" rel="stylesheet">
<style>
  :root {
    --stage: #2e2f31;
    --paper: #ffffff;
    --ink: #2a2a2a;
    --ink-soft: #555555;
    --green: #58b047;
    --lime: #c4d53f;
    --rule: #cfcfcf;
  }
  * { box-sizing: border-box; margin: 0; padding: 0; }
  html, body { width: 1200px; height: 856px; overflow: hidden; }
  body { background: var(--stage); position: relative; font-family: "Open Sans", sans-serif; color: var(--ink); }

  .letterhead {
    position: absolute; left: 78px; top: 73px; width: 504px; height: 713px;
    background: var(--paper); box-shadow: 0 8px 18px rgba(0,0,0,.45);
  }
  .wordmark { font-family: "Mada", sans-serif; font-weight: 500; color: var(--ink); line-height: .86; display: flex; align-items: center; gap: 6px; }
  .wordmark .dot { width: 22px; height: 22px; border-radius: 50%; background: var(--green); flex: none; }
  .letterhead .wordmark { position: absolute; right: 37px; top: 52px; font-size: 24px; }
  .letterhead .wordmark .stack { text-align: right; }

  .return-line { position: absolute; left: 52px; top: 114px; font-size: 4.6px; border-bottom: .6px solid var(--ink-soft); padding-bottom: 1.5px; color: var(--ink-soft); }
  .recipient { position: absolute; left: 52px; top: 132px; font-size: 7.6px; line-height: 10.2px; }
  .recipient .city { margin-top: 10px; }
  .subject { position: absolute; left: 52px; top: 242px; font-size: 7.4px; font-weight: 700; }
  .body-copy { position: absolute; left: 52px; top: 270px; width: 278px; font-size: 7.1px; line-height: 9.2px; }
  .body-copy p + p { margin-top: 9px; }
  .closing { position: absolute; left: 52px; top: 502px; font-size: 7.1px; color: var(--ink-soft); }
  .signature { position: absolute; left: 52px; top: 520px; width: 106px; height: 22px; }
  .signer { position: absolute; left: 52px; top: 552px; font-size: 7.1px; color: var(--ink-soft); }

  .footer-rule { position: absolute; left: 52px; right: 38px; top: 658px; height: 1px; background: linear-gradient(90deg, var(--green), var(--lime)); }
  .footer { position: absolute; left: 52px; top: 666px; font-size: 4.8px; line-height: 7.9px; color: var(--ink); }
  .footer .col { position: absolute; top: 0; white-space: nowrap; }
  .footer strong { font-weight: 700; }

  .card { position: absolute; top: 273px; width: 198px; height: 307px; box-shadow: 0 8px 18px rgba(0,0,0,.45); }
  .card-front { left: 651px; background: var(--paper); font-family: "Mada", sans-serif; }
  .card-front .wordmark { position: absolute; left: 34px; top: 40px; font-size: 25px; }
  .card-divider { position: absolute; left: 35px; top: 139px; width: 93px; height: 1.5px; background: var(--rule); }
  .contact { position: absolute; left: 34px; top: 160px; font-size: 9.2px; line-height: 11.4px; color: var(--ink-soft); letter-spacing: .2px; }
  .contact .name { font-weight: 600; color: var(--ink); }
  .contact .role { color: var(--green); }
  .contact .gap { margin-top: 8px; }
  .contact .web { font-weight: 600; color: var(--ink); }

  .card-back { left: 903px; background: linear-gradient(180deg, var(--lime) 0%, #a6cc45 40%, var(--green) 100%); display: flex; align-items: center; justify-content: center; }
  .card-back .wordmark { color: #ffffff; font-size: 30px; flex-direction: column; gap: 8px; text-align: center; }
  .card-back .wordmark .dot { background: #ffffff; width: 30px; height: 30px; }
</style>
</head>
<body>

<section class="letterhead">
  <div class="wordmark"><span class="dot"></span><span class="stack">veranto<br>events</span></div>

  <div class="return-line">Vorname Nachname, Musterstr. 123, 12345 Musterstadt</div>
  <address class="recipient" style="font-style:normal">
    Martina Musterfrau<br>Musterstraße 456
    <div class="city">12345 Berlin</div>
  </address>

  <div class="subject">Quidero molore, atatur sae. Nequat,</div>

  <div class="body-copy">
    <p>Ur sit, imus, ipicatem voluptate eum re dolluptios sequosam, eum reritati am volor sapedissi quo blaboribust, sequass itasped igendi cus exerfer feruptas iusanda ndaest, qui omnis nus aut fugitinis quatur ad ullaut mostem quasperiae corem et aciatem illatin ciduntores quidis utemquam autemperae soluptiae lab illacescia solorum et fugiam ratatatus exerro blaciis samusam etur? Uga. Neque nam simi, nest, ommod essedios magnatia nossi aute nonsequam fugiaspis moluptas sed el int etur saepe nonsecatem excea noneceperrum ulligendit faccullores et lantur si ium at.Ota cuptae non ea de opta voles rem rae dolore ilia vellab isi blanis idit veribus auda alit labore desenis imenis que in con rehent, explat ped que volorum, autent, si tetur?</p>
    <p>Ihil ium restior ecepero reptistius es aborepe diatiunt dignis diciae voluptu ribearit, que nat aute et as maximus, qui blab iur aut volest, nonsequae odios doluptatiae velignimin perescia vent.<br>Pa voluptas expero corectur molest eaquid enda vidus verciis quodi te dit aliquid unturem poreper feratur? Quis aut rehenihilit et quam, eris et perorru mquamusa quo et untia volupie nisimoluptae esseribus cora doluptati doluptatur atisciumqui re pa quat aut lam solescia intiis et millabor sit odis et quos re sam, vendicientur abo. Equi totatus rest, nosam quodi omni doloriosam des ea nimpelique volo elendae dellign ihilitis solupta temporp orupta iuntia ipiste natibusapis volesedis reriori taerrup tatiberes nobitiur, sequi omnihillab id maximagnat omnimus dolo quunt, int aut earum lacit peliquunt iduciet, id que automolum deruptati te non re.</p>
  </div>

  <div class="closing">Sincerely</div>
  <svg class="signature" viewBox="0 0 106 22" role="img" aria-label="Handschriftliche Unterschrift">
    <path d="M2 18 C6 8 8 3 10 4 C11 10 10 15 11 16 C14 10 17 4 19 5 C19 10 19 14 21 16 M26 17 l1 0 M32 18 C36 8 38 3 40 4 C41 10 40 15 41 16 C44 10 47 4 49 5 C49 10 49 14 51 16 C54 11 56 11 56 16 C58 11 60 11 60 16 C62 12 65 11 65 16 C66 12 68 12 68 16 C70 12 73 11 73 16 C74 12 77 12 77 16 C79 12 82 11 84 15" fill="none" stroke="#1f1f1f" stroke-width="1.1" stroke-linecap="round"/>
  </svg>
  <div class="signer">Max Mustermann</div>

  <div class="footer-rule"></div>
  <footer class="footer">
    <div class="col" style="left:0"><strong>Veranto Events UG</strong><br>(haftungsbeschränkt)<br>Lindenweg 8b<br>45990 Talbach</div>
    <div class="col" style="left:71px">T: (02 31) 482 19 306<br>F: (02 31) 482 19 307<br>kontakt@veranto-events.de<br>www.veranto-events.de</div>
    <div class="col" style="left:159px">Geschäftsführer:<br>Gesmo Darlan<br>Sitz der Gesellschaft:<br>Talbach</div>
    <div class="col" style="left:231px">Eingetragen beim<br>Amtsgericht Talbach<br>HR B 41 92<br>USt.-Id.-Nr. DE 104 587 336</div>
    <div class="col" style="left:323px">Kreisbank Talgrund<br>IBAN DE00123400005678901200<br>BIC KRTLDE31XXX</div>
  </footer>
</section>

<section class="card card-front">
  <div class="wordmark"><span class="dot"></span><span class="stack">veranto<br>events</span></div>
  <div class="card-divider"></div>
  <div class="contact">
    <div class="name">Vorname Nachname</div>
    <div class="role">Geschäftsführung</div>
    <div class="gap">Musterstr. 123<br>12345 Musterstadt</div>
    <div class="gap">T: 010 / 123 456 789<br>F: 010 / 123 456 790<br>info@beispielnetz.de</div>
    <div class="gap web">www.beispielnetz.de</div>
  </div>
</section>

<section class="card card-back">
  <div class="wordmark"><span class="dot"></span><span>veranto<br>events</span></div>
</section>

</body>
</html>
```